Business card design Needed for new logo / Construction business, home extensions and new builds

We need a business card design using our new logo files which i will attach to this project :)

We are a small construction business specialising in home extensions, new builds and property development. We are very ambitious and would appreciate professional and elegant designs for our new business card.

Very serious about using the services on MakerQuarry and recently acquired our new logo from here :)

Please get involved, i will feedback when i can as i am very busy but can respond daily, thanks

Target Market(s)

People that want to build onto their houses, new building developments or adding too their existing property

Industry/Entity Type

Construction

Contact Information for Business Card

Renwick Tolliver Construction, Lionel Ashby (Managing Director), Tel 07822254961, email - info@renwick-tolliver, www.renwick-tolliver.co.uk

Colors

Designer to choose colors to be used in the design.

Requirements
Must have
• I like a deep grey on the back please. A lot of you have provided black from and back, try mixing things up a little. The black looks cool 😎 Thanks

```html
<!DOCTYPE html>
<html lang="en">
<head>
<meta charset="utf-8">
<title>Renwick Tolliver Construction – Business Card</title>
<link rel="stylesheet" href="https://fonts.googleapis.com/css2?family=Open+Sans:wght@400;600;700&display=swap">
<style>
  :root {
    --page: #2a2a2c;
    --card-black: #1e1e21;
    --card-grey: #8e9296;
    --grey-light: #b4b8bb;
    --gold: #d9a62e;
    --gold-deep: #b07d17;
    --white: #f2f2f2;
    --text-soft: #dcdcdc;
  }
  * { box-sizing: border-box; margin: 0; padding: 0; }
  html, body { width: 1200px; height: 780px; overflow: hidden; }
  body {
    background: var(--page);
    font-family: "Open Sans", Arial, sans-serif;
    position: relative;
  }
  .card {
    position: absolute;
    top: 222px;
    width: 520px;
    height: 336px;
    border-bottom: 3px solid var(--gold);
    border-left: 3px solid var(--gold);
    overflow: hidden;
  }
  .card--front { left: 50px; background: var(--card-black); }
  .card--back { left: 630px; background: var(--card-grey); }

  .brand {
    position: absolute;
    left: 70px;
    top: 42px;
    display: flex;
    align-items: center;
    gap: 12px;
  }
  .brand__square {
    width: 18px; height: 18px;
    background: var(--gold);
  }
  .brand__name {
    color: var(--gold);
    font-weight: 600;
    font-size: 17px;
    letter-spacing: 1.5px;
    text-transform: uppercase;
    line-height: 1.3;
  }
  .address {
    position: absolute;
    left: 40px;
    top: 118px;
    color: var(--text-soft);
    font-size: 14px;
    line-height: 1.45;
  }
  .contacts {
    position: absolute;
    left: 28px;
    top: 178px;
    list-style: none;
    color: var(--white);
    font-size: 14px;
    line-height: 1.7;
  }
  .contacts li { display: flex; align-items: center; gap: 9px; }
  .contacts svg { width: 12px; height: 12px; fill: var(--gold); flex: none; }

  .person {
    position: absolute;
    right: 38px;
    top: 112px;
    text-align: right;
  }
  .person__name {
    font-size: 30px;
    font-weight: 700;
    letter-spacing: 0.5px;
    color: var(--white);
  }
  .person__name .surname { color: var(--gold); }
  .person__title {
    font-size: 15px;
    color: var(--white);
    letter-spacing: 0.5px;
  }
  .edge-tab {
    position: absolute;
    right: 0;
    top: 112px;
    width: 14px;
    height: 64px;
    background: linear-gradient(90deg, var(--gold-deep), var(--gold));
  }
  .emboss-mark {
    position: absolute;
    right: 90px;
    bottom: 34px;
    width: 120px;
    height: 120px;
    background: #18181a;
  }

  .back-pattern {
    position: absolute;
    inset: 0;
    background: linear-gradient(135deg, var(--card-grey) 0%, var(--grey-light) 60%, #a4a8ab 100%);
  }
  .back-brand {
    position: absolute;
    right: 26px;
    bottom: 22px;
    color: var(--white);
    font-weight: 600;
    font-size: 9px;
    letter-spacing: 1px;
    text-transform: uppercase;
  }
</style>
</head>
<body>

<section class="card card--front">
  <div class="brand">
    <span class="brand__square"></span>
    <span class="brand__name">Renwick Tolliver<br>Construction</span>
  </div>

  <p class="address">Calder Road, Eastwick<br>Fernbrook, FB4 2LT</p>

  <ul class="contacts">
    <li>
      <svg viewBox="0 0 24 24" aria-hidden="true"><path d="M6.6 10.8a15 15 0 0 0 6.6 6.6l2.2-2.2a1 1 0 0 1 1-.25 11.4 11.4 0 0 0 3.6.57 1 1 0 0 1 1 1V20a1 1 0 0 1-1 1A17 17 0 0 1 3 4a1 1 0 0 1 1-1h3.5a1 1 0 0 1 1 1c0 1.25.2 2.45.57 3.6a1 1 0 0 1-.25 1z"/></svg>
      0782 225 4961
    </li>
    <li>
      <svg viewBox="0 0 24 24" aria-hidden="true"><path d="M2 5h20v14H2z M2 5l10 8 10-8" /></svg>
      info@renwick-tolliver.co.uk
    </li>
    <li>
      <svg viewBox="0 0 24 24" aria-hidden="true"><circle cx="12" cy="12" r="10"/></svg>
      www.renwick-tolliver.co.uk
    </li>
  </ul>

  <div class="person">
    <p class="person__name">Lionel <span class="surname">Ashby</span></p>
    <p class="person__title">Managing Director</p>
  </div>
  <span class="edge-tab"></span>
  <span class="emboss-mark"></span>
</section>

<section class="card card--back">
  <div class="back-pattern" role="img" aria-label="Repeating silver spot-gloss brand pattern on deep grey"></div>
  <span class="back-brand">Renwick Tolliver Construction</span>
</section>

</body>
</html>
```